Simple Logo Design for Semi-Clear Plastic Frosted Card stock

Create a business card on frosted plastic. compliment existing logo elements with a tree trunk, roots, or seed at the lower half and the full logo both on the front.

Contact information will go on a solid portion of the back of this design since this card stock is semi-transparent.

It is important to consider this plastic card stock medium in your design. I found helpful tips and guides listed at vellaprint-sample.net: be careful to understand ink printed on plastic cards cannot have too much of a consistent print area or risks peeling and fine lines can easily scratch off.
Updates

2" x 3.5" 20PT Clear Plastic Business cards with Round corners Please get info or templates here: https://www.vellaprint-sample.net/product-detail/2-x-35-20pt-clear-plastic-business-cards-with-round-corners

Target Market(s)

Not for profit- religion

Industry/Entity Type

Business

Must include complementary elements to the existing logo

Font styles to use
Decorative

Colors
000000

Requirements
Must have
• Elements of community, nature and oneness. Such as: seed, roots, tree trunk, etc.
• Three lines of space on the back for Name, Title, Phone Number.
Nice to have
• I like a light use of decorative elements
Should not have
• No eyes, from faces or animals.

```html
<!DOCTYPE html>
<html lang="en">
<head>
<meta charset="utf-8">
<title>Steadfast Path – Business Card</title>
<link rel="stylesheet" href="https://fonts.googleapis.com/css2?family=Josefin+Sans:wght@400;600&family=Crimson+Text:wght@400&family=Arimo:wght@400&display=swap">
<style>
  :root {
    --page-bg: #e4e1dc;
    --frost-light: #f3f4f3;
    --frost-mid: #dfe3e3;
    --brand-green: #2f6b5e;
    --tagline: #4a4f4d;
    --band-black: #141615;
    --panel-green: #2f5f57;
    --panel-green-deep: #244a45;
    --panel-text: #efd3d4;
    --panel-text-soft: #d9b9bd;
  }
  * { margin: 0; padding: 0; box-sizing: border-box; }
  html, body {
    width: 1200px;
    height: 970px;
    overflow: hidden;
    background: var(--page-bg);
  }
  .canvas {
    position: relative;
    width: 1200px;
    height: 970px;
  }
  .card {
    position: absolute;
    left: 100px;
    top: 185px;
    width: 1000px;
    height: 600px;
    border-radius: 30px;
    overflow: hidden;
    background: linear-gradient(180deg, var(--frost-light) 0%, var(--frost-mid) 100%);
    box-shadow: 0 10px 30px rgba(0,0,0,0.12);
  }
  .brand {
    position: absolute;
    left: 0;
    top: 0;
    width: 100%;
    height: 355px;
    text-align: center;
  }
  .brand-dot {
    position: absolute;
    left: 50%;
    top: 80px;
    width: 120px;
    height: 120px;
    margin-left: -60px;
    border-radius: 50%;
    background: var(--brand-green);
  }
  .brand-name {
    position: absolute;
    left: 0;
    right: 0;
    top: 234px;
    font-family: "Josefin Sans", sans-serif;
    font-weight: 400;
    font-size: 54px;
    line-height: 1;
    letter-spacing: 2px;
    color: var(--brand-green);
    white-space: nowrap;
  }
  .brand-tagline {
    position: absolute;
    left: 0;
    right: 0;
    top: 300px;
    font-family: "Josefin Sans", sans-serif;
    font-weight: 600;
    font-size: 19px;
    line-height: 1;
    letter-spacing: 1.5px;
    color: var(--tagline);
    white-space: nowrap;
  }
  .divider-band {
    position: absolute;
    left: 0;
    top: 355px;
    width: 100%;
    height: 32px;
    background: var(--band-black);
  }
  .contact-panel {
    position: absolute;
    left: 0;
    top: 387px;
    width: 100%;
    height: 213px;
    background: linear-gradient(180deg, var(--panel-green) 0%, var(--panel-green-deep) 100%);
    text-align: center;
  }
  .person-name {
    position: absolute;
    left: 0; right: 0;
    top: 20px;
    font-family: "Crimson Text", serif;
    font-size: 48px;
    line-height: 1.1;
    color: var(--panel-text);
  }
  .person-title {
    position: absolute;
    left: 0; right: 0;
    top: 88px;
    font-family: "Arimo", sans-serif;
    font-size: 27px;
    line-height: 1.1;
    color: var(--panel-text-soft);
  }
  .person-phone {
    position: absolute;
    left: 0; right: 0;
    top: 150px;
    font-family: "Arimo", sans-serif;
    font-size: 27px;
    line-height: 1.1;
    color: var(--panel-text-soft);
  }
</style>
</head>
<body>
  <main class="canvas">
    <article class="card">
      <header class="brand">
        <div class="brand-dot"></div>
        <div class="brand-name">STEADFAST PATH</div>
        <div class="brand-tagline">WISDOM, FELLOWSHIP &amp; CALM</div>
      </header>
      <div class="divider-band"></div>
      <section class="contact-panel">
        <div class="person-name">Martin Ellery</div>
        <div class="person-title">Managing Director</div>
        <div class="person-phone">0400 183 927</div>
      </section>
    </article>
  </main>
</body>
</html>
```